Tall Fern Roofing Business Card

Need a business card with the logo that was designed here

Contact Information for Business Card

Name, Title, Phone, Email, Website, Company name

```html
<!DOCTYPE html>
<html lang="en">
<head>
<meta charset="utf-8">
<title>Tall Fern Roofing – Business Card</title>
<link rel="stylesheet" href="https://fonts.googleapis.com/css2?family=Poppins:wght@400;700&display=swap">
<style>
  :root {
    --brand-blue: #1c76bd;
    --roof-grey: #939598;
    --ink: #4a4a4a;
    --paper: #ffffff;
    --backdrop: #2c2c2c;
    --rule: #dddddd;
  }
  * { margin: 0; padding: 0; box-sizing: border-box; }
  html, body { width: 1093px; height: 1200px; overflow: hidden; }
  body {
    background: var(--backdrop);
    font-family: "Poppins", sans-serif;
    position: relative;
  }
  .card {
    position: absolute;
    left: 264px;
    width: 580px;
    height: 357px;
    overflow: hidden;
  }
  .card--front { top: 226px; background: var(--paper); }
  .card--back { top: 620px; background: var(--brand-blue); }

  .roof-band {
    position: absolute; left: 0; top: 0;
    width: 100%; height: 150px;
    background: linear-gradient(90deg, var(--brand-blue) 0%, var(--brand-blue) 55%, var(--roof-grey) 100%);
  }

  .person { position: absolute; left: 31px; top: 204px; }
  .person__name {
    color: var(--brand-blue); font-weight: 700; font-size: 21px; line-height: 1;
  }
  .person__title {
    color: var(--ink); font-size: 16px; line-height: 1.2; margin-top: 2px;
  }
  .divider {
    position: absolute; left: 31px; top: 257px;
    width: 300px; height: 1px; background: var(--rule);
  }
  .contact { position: absolute; left: 31px; top: 274px; list-style: none; }
  .contact__item {
    display: flex; align-items: center; gap: 7px;
    color: var(--ink); font-size: 16px; line-height: 21px;
  }
  .contact__item svg { width: 15px; height: 15px; fill: var(--brand-blue); }

  .wordmark {
    display: flex; align-items: center; gap: 8px;
    font-weight: 700; white-space: nowrap;
  }
  .wordmark__square { display: block; background: currentColor; }
  .card--front .wordmark {
    position: absolute; right: 32px; top: 200px;
    color: var(--brand-blue); font-size: 22px;
  }
  .card--front .wordmark__square { width: 14px; height: 14px; }

  .website {
    position: absolute; right: 32px; top: 287px;
    font-size: 16px; color: var(--ink);
  }
  .website__domain { color: var(--brand-blue); }

  .card--back .wordmark {
    position: absolute; left: 0; right: 0; top: 0; bottom: 0;
    justify-content: center; color: var(--paper); font-size: 40px;
  }
  .card--back .wordmark__square { width: 26px; height: 26px; }
</style>
</head>
<body>
  <section class="card card--front">
    <div class="roof-band" role="img" aria-label="Large roofline illustration in blue and grey with a window and chimney"></div>

    <div class="person">
      <p class="person__name">MARCUS HALE</p>
      <p class="person__title">Managing Director</p>
    </div>
    <div class="divider"></div>

    <ul class="contact">
      <li class="contact__item">
        <svg viewBox="0 0 24 24" aria-hidden="true"><path d="M6.6 10.8a15.1 15.1 0 0 0 6.6 6.6l2.2-2.2a1 1 0 0 1 1-.25 11.4 11.4 0 0 0 3.6.57 1 1 0 0 1 1 1V20a1 1 0 0 1-1 1A17 17 0 0 1 3 4a1 1 0 0 1 1-1h3.5a1 1 0 0 1 1 1c0 1.25.2 2.45.57 3.57a1 1 0 0 1-.25 1z"/></svg>
        044-555 218 730
      </li>
      <li class="contact__item">
        <svg viewBox="0 0 24 24" aria-hidden="true"><path d="M2 5h20v14H2z M3 6l9 7 9-7" stroke="#fff" stroke-width="1.4"/></svg>
        info@tallfernroof.com
      </li>
    </ul>

    <p class="wordmark"><span class="wordmark__square"></span>Tall Fern Roofing</p>

    <p class="website">www.<span class="website__domain">tallfernroof</span>.com</p>
  </section>

  <section class="card card--back">
    <p class="wordmark"><span class="wordmark__square"></span>Tall Fern Roofing</p>
  </section>
</body>
</html>
```